Weightloss company needs Business Card

We want a business card that is clean and professional, yet portrays that we are a friendly, innovative, and versatile program designed to fit the needs of our clients.
I would like there to be 2 sides, one side having an appointment card, and the other side containing the logo and business information. There can be decorations on both sides. The logo is attached.

Target Market(s)

Men and women 40-60

Industry/Entity Type

Business

Contact Information for Business Card

Font styles to use
Sans Serif

Requirements
Must have
• The logo, space for business information
Nice to have
• The colors in the logo
Should not have
• No pictures of people or food

```html
<!DOCTYPE html>
<html lang="en">
<head>
<meta charset="utf-8">
<title>Brightpath Wellness – Business Card</title>
<link href="https://fonts.googleapis.com/css2?family=Source+Sans+3:wght@400;700&display=swap" rel="stylesheet">
<style>
  :root {
    --backdrop: #3a332e;
    --card: #0e0e0e;
    --accent-red: #f0194a;
    --accent-cyan: #35c2e0;
    --text-light: #f2f2f2;
    --silver: #c9c9c9;
  }
  * { box-sizing: border-box; margin: 0; padding: 0; }
  html, body {
    width: 1200px; height: 900px; overflow: hidden;
    background: var(--backdrop);
    font-family: "Source Sans 3", sans-serif;
  }
  .sheet {
    position: relative; width: 1200px; height: 900px;
    display: flex; align-items: center; justify-content: center; gap: 60px;
  }
  .card {
    position: relative;
    width: 520px; height: 298px;
    background: var(--card);
    box-shadow: 0 14px 30px rgba(0,0,0,.45);
  }
  /* Front: brand + contact */
  .card-front { display: flex; align-items: center; }
  .brand {
    width: 262px; display: flex; align-items: center; justify-content: center; gap: 10px;
  }
  .brand-name {
    color: var(--accent-red); font-weight: 700; font-size: 25px; line-height: 1.05;
  }
  .brand-dot {
    width: 14px; height: 14px; border-radius: 50%; background: var(--accent-red); flex: none;
  }
  .divider {
    width: 1px; height: 132px; background: var(--accent-red); opacity: .8;
  }
  .contact {
    padding-left: 20px; color: var(--text-light); font-size: 14px; line-height: 1.3;
  }
  .contact-name { color: var(--accent-red); font-weight: 700; font-size: 16px; }
  .contact-role { margin-bottom: 12px; }
  .contact-address { margin-bottom: 12px; }
  .contact-list { list-style: none; }
  .contact-list li { display: flex; align-items: center; gap: 8px; }
  .contact-list svg { width: 10px; height: 10px; flex: none; }
  /* Back: brand only */
  .card-back { display: flex; align-items: center; justify-content: center; gap: 14px; }
  .card-back .brand-name { color: var(--silver); font-size: 36px; }
  .card-back .brand-dot { background: var(--silver); width: 18px; height: 18px; }
</style>
</head>
<body>
<main class="sheet">
  <section class="card card-front" aria-label="Business card front">
    <div class="brand">
      <span class="brand-dot"></span>
      <span class="brand-name">Brightpath<br>Wellness</span>
    </div>
    <div class="divider"></div>
    <div class="contact">
      <p class="contact-name">Daniel Carter</p>
      <p class="contact-role">Managing Director</p>
      <p class="contact-address">4820 Maple Ridge Road<br>Lakeview, 560218.</p>
      <ul class="contact-list">
        <li><svg viewBox="0 0 10 10"><path d="M2 0.5 L4 2.5 L3 3.8 Q4.5 6 6.2 7 L7.5 6 L9.5 8 L8 9.5 Q3 9 0.5 2 Z" fill="var(--accent-red)"/></svg>055-274 918 360</li>
        <li><svg viewBox="0 0 10 10"><rect x="0.5" y="2" width="9" height="6.5" fill="var(--accent-red)"/><path d="M0.5 2 L5 5.5 L9.5 2" stroke="var(--card)" fill="none"/></svg>hello@brightpathwell.com</li>
        <li><svg viewBox="0 0 10 10"><circle cx="5" cy="5" r="4.5" fill="var(--accent-red)"/><path d="M0.5 5 H9.5 M5 0.5 Q2 5 5 9.5 Q8 5 5 0.5" stroke="var(--card)" fill="none" stroke-width=".8"/></svg>www.brightpathwell.com</li>
      </ul>
    </div>
  </section>
  <section class="card card-back" aria-label="Business card back">
    <span class="brand-dot"></span>
    <span class="brand-name">Brightpath<br>Wellness</span>
  </section>
</main>
</body>
</html>
```